Design Website to Recruit next Generation of Steel Harbor's Order Vantage

Design a cool website that provides just enough information to be intriguing to teenagers who compete in combat sports. The format is to make this an invite-only team of high-school-aged competitors in combat sports (predominately Jiu Jitsu right now). Cinder Ravens can participate in similar assignments to earn consideration. We are modeled after the Order Vantage formed in Steel Harbor and would like to keep that look and feel. The document attached "OV - Ideas and Content for Website" shows our initial thoughts and here is more about us:

Goal - To promote the success of committed teenage Jiu Jitsu competitors who excel through focused preparation and deliberate practice.

Why - Prove the core principles of success.

How - Success is its own reward and always entails an element of the unknown/uncontrollable. We reward preparation. Setting clear goals (SMART), deliberate practice, building mental models (domain specific knowledge), restorative recovery, nutritional coaching, power of teaching others, sports science (strength & conditioning), expert guidance, personalized development plans, accountability, Quantified Self, gamification and competitive challenges. What - We will win at the highest of levels across the fight world by applying the general principles of success. These lessons will be carried with them to other areas of their lives.

Our primary goal with the website would be to share our company’s mission statement and promote the success of our sponsored athletes.

The only social media account we have currently is Pixtrelle's @ordervantageK7 (recently established). If you want more of an idea for what our online presence should feel like, then I would suggest watching these two scenes from Steel Harbor:

Recruiting: This scene shows the process for joining Order Vantage: https://vidrelo.net/Qk82LmTrA

Order Vantage Assignments: This shows how assignments are handed out for members to accomplish: https://vidrelo.net/Zp41XwNeB

Order Vantage Color Assignment: This is their first large assignment and where the green color comes from: https://vidrelo.net/Hd67VcJuC

It is also worth noting that "less is more" considering the first rule is, "you do not talk about..." That should carry over to our website and social media presence. We want to share just enough to be intriguing to inquiring minds and motivational for members, but no more.

I have uploaded a bunch of content, but just wanted to give you a broader idea. Feel free to design as you see fit...
Updates

Please stay tuned for the "burning smiley face" files. I have purchased a rendering of it so we have a proprietary vector image to use on our site. There will also be files for different versions of the Order Vantage//OV logos for various subcategories. Here is how they are to be applied: Circled = Primary (for main/landing page), Jiu Jitsu = Pyramid, Wrestling = Traditional, Muay Thai = Rolled, and Legacy OV = Original (coming soon).

Target Market(s)

Teenage competitors of combat sports, their parents, and sponsors of those athletes

Industry/Entity Type

Martial Arts & High School Sports

Coding

Coded - Design and coding required

Number of Pages Required

5+ page

Font styles to use
Sans Serif
Other font styles liked:
• See font in "Circled Logo"

Colors
59FF00
82FF00
B8FF75
E3FFCB
F4FFEA
EB3D1F
EC4F4E
F09395
F8D3D4
FCEDEE

Requirements
Must have
• Cool landing page with logo and brief summary of what we do. Page with 8 rules and explanation for earning an invitation. Plus, accomplishments page for memorializing the success of sponsored "Cinder Ravens"
Should not have
• Individual names

```html
<!DOCTYPE html>
<html lang="en">
<head>
<meta charset="utf-8">
<title>Order Vantage</title>
<link rel="stylesheet" href="https://fonts.googleapis.com/css2?family=Poppins:wght@400;500;600;700;800&family=Bowlby+One&display=swap">
<style>
:root{
  --orange:#d95b35;
  --orange-dark:#b9472a;
  --ink:#1e1e1e;
  --text:#222;
  --grey-line:#d9d9d9;
  --shadow:rgba(0,0,0,.18);
  --white:#fff;
  --black:#000;
}
*{box-sizing:border-box;margin:0;padding:0}
html,body{width:1200px;height:4721px;overflow:hidden}
body{position:relative;font-family:"Poppins",sans-serif;color:var(--text);background:var(--white)}
.abs{position:absolute}

/* header */
.site-header{position:absolute;left:0;top:0;width:1200px;height:158px;border-bottom:1px solid var(--grey-line)}
.header-band{position:absolute;left:0;top:0}
.brand{position:absolute;left:134px;top:34px;font-family:"Poppins",sans-serif;font-weight:700;font-size:44px;line-height:52px;color:var(--orange);letter-spacing:1px}
.search{position:absolute;left:821px;top:13px;width:264px;height:33px;border:2px solid var(--white);border-radius:4px;color:var(--white);font-size:13px;letter-spacing:1px;padding:6px 0 0 9px}
.search svg{position:absolute;right:10px;top:7px}
.menu-btn{position:absolute;left:1033px;top:88px;width:53px;height:49px;background:var(--orange);padding:14px 10px}
.menu-btn span{display:block;height:2px;background:var(--white);margin-bottom:7px}

/* hero */
.hero{position:absolute;left:0;top:158px;width:1200px;height:520px;background:radial-gradient(ellipse at 50% 45%,#e9e9ea 0%,#a3a4a8 28%,#55575d 60%,#2a2b30 100%);text-align:center}
.hero-title{position:absolute;left:0;right:0;top:106px;font-family:"Bowlby One",sans-serif;font-size:46px;color:var(--white);-webkit-text-stroke:1.5px var(--orange);text-shadow:3px 3px 0 rgba(0,0,0,.35);letter-spacing:1px}
.hero-sub{position:absolute;left:0;right:0;top:186px;font-weight:700;font-size:25px;line-height:38px;color:var(--ink)}

/* about */
.about-photo{position:absolute;left:0;top:758px;width:695px;height:508px;background:linear-gradient(120deg,#cfc7bd 0%,#f1ede8 35%,#9e8f80 70%,#c9604c 100%);clip-path:polygon(0 0,595px 0,693px 254px,595px 508px,0 508px)}
.about-edge{position:absolute;left:590px;top:758px}
.outline-heading{font-family:"Bowlby One",sans-serif;color:var(--white);-webkit-text-stroke:1.3px var(--orange);text-shadow:2px 2px 0 #9b9b9b}
.about-heading{position:absolute;left:709px;top:748px;font-size:29px;line-height:52px}
.about-text{position:absolute;left:710px;top:866px;width:430px;font-size:21px;line-height:38.5px}
.about-quote{position:absolute;left:740px;top:1231px;font-size:27px}

/* pillars */
.pillar{position:absolute;width:396px;height:396px;border:6px solid var(--orange);border-radius:50%;background:var(--white);box-shadow:inset 0 0 0 12px var(--white),inset 14px 14px 28px rgba(0,0,0,.22)}
.pillar-title{position:absolute;left:0;right:0;text-align:center;top:95px;font-weight:700;font-size:26px;color:var(--orange)}
.pillar-list{list-style:none;position:absolute;left:0;top:150px;width:100%}
.pillar-list li{height:62.5px;display:flex;align-items:center;font-size:23px;color:var(--ink)}
.pillar-list li svg{margin-right:20px;flex:none}
.pillar-tech{left:198px;top:1355px;z-index:1}
.pillar-tech .pillar-list{padding-left:100px}
.pillar-spirit{left:593px;top:1355px;z-index:1}
.pillar-spirit .pillar-list{padding-left:104px}
.pillar-body{left:401px;top:1694px;z-index:2}
.pillar-body .pillar-list{padding-left:100px}

/* rules */
.scars-heading{position:absolute;left:0;right:0;top:2172px;text-align:center;font-size:29px}
.scars-text{position:absolute;left:214px;top:2233px;width:790px;font-size:20px;line-height:38.5px;text-transform:uppercase}
.rule-card{position:absolute;width:445px;height:156px;border-radius:78px;background:var(--white);box-shadow:0 4px 14px var(--shadow)}
.rule-badge{position:absolute;left:14px;top:21px;width:114px;height:114px;border-radius:50%;background:var(--orange);color:var(--white);font-weight:700;font-size:28px;line-height:46px;text-align:center;padding-top:11px}
.rule-text{position:absolute;left:156px;top:21px;width:250px;font-size:21px;line-height:38.5px}

/* faq */
.faq-heading{position:absolute;left:0;right:0;top:3185px;text-align:center;font-size:29px}
.faq-q{position:absolute;left:165px;width:870px;height:59px;background:var(--white);box-shadow:0 2px 8px var(--shadow);color:var(--orange);font-size:24px;line-height:59px;padding-left:40px}
.faq-q svg{position:absolute;right:20px;top:22px}
.faq-a{position:absolute;left:207px;width:830px;font-size:20.5px;line-height:38.5px}
.view-more{position:absolute;left:507px;top:3734px;width:186px;height:53px;background:var(--orange);color:var(--white);font-weight:700;font-size:20px;line-height:53px;text-align:center;box-shadow:4px 4px 0 #3a3a3a}

/* video */
.video{position:absolute;left:0;top:3875px;width:1200px;height:518px;background:linear-gradient(100deg,#7a3414 0%,#e07a2c 25%,#3c3235 55%,#274d80 80%,#1b2a44 100%)}
.video-play{position:absolute;left:520px;top:226px;display:flex;align-items:center;gap:12px;color:var(--white);font-weight:600;font-size:24px}
.video-play span.dot{width:46px;height:46px;border-radius:50%;background:var(--white)}

/* footer */
.site-footer{position:absolute;left:0;top:4393px;width:1200px;height:328px;background:var(--black);text-align:center}
.footer-brand{position:absolute;left:0;right:0;top:48px;font-weight:700;font-size:44px;line-height:52px;color:var(--orange);letter-spacing:1px}
.social{position:absolute;left:0;right:0;top:193px;display:flex;justify-content:center;gap:26px;color:var(--white);font-size:17px}
.social span{display:flex;align-items:center;gap:7px}
.social i{display:block;width:16px;height:16px;border-radius:50%;background:var(--orange)}
.copyright{position:absolute;left:0;right:0;top:255px;color:var(--white);font-size:19px}
</style>
</head>
<body>

<header class="site-header">
  <svg class="header-band" width="1200" height="60" viewBox="0 0 1200 60"><polygon points="403,0 1200,0 1200,60 430,60" fill="var(--orange)"/></svg>
  <div class="brand">ORDER<br>VANTAGE</div>
  <div class="search">SEARCH
    <svg width="16" height="16" viewBox="0 0 16 16"><circle cx="6.5" cy="6.5" r="5" fill="none" stroke="#fff" stroke-width="1.6"/><line x1="10.3" y1="10.3" x2="15" y2="15" stroke="#fff" stroke-width="1.6"/></svg>
  </div>
  <div class="menu-btn"><span></span><span></span><span></span></div>
</header>

<section class="hero" role="img" aria-label="Two gloved fists meeting in a burst of smoke and sparks">
  <h1 class="hero-title">DORIAN BUILT HIMSELF AN ARMY</h1>
  <p class="hero-sub">HOW MUCH CAN YOU KNOW ABOUT YOURSELF<br>IF YOU'VE NEVER BEEN IN A FIGHT?</p>
</section>

<section class="about">
  <div class="about-photo" role="img" aria-label="Martial artists in white uniforms training on a mat"></div>
  <svg class="about-edge" width="110" height="508" viewBox="0 0 110 508"><polyline points="5,0 103,254 5,508" fill="none" stroke="var(--orange)" stroke-width="4"/></svg>
  <h2 class="about-heading outline-heading">WHY WAS DORIAN BUILDING<br>AN ARMY?</h2>
  <p class="about-text">Lorem ipsum dolor sit amet, consectetur adipiscing elit, sed do eiusmod tempor incididunt ut labore et dolore magna aliqua. Ut enim ad minim veniam, quis nostrud exercitation ullamco laboris nisi ut aliquip ex ea commodo consequat. Duis aute irure dolor in reprehenderit in voluptate velit esse cillum dolore eu fugiat nulla pariatur. Excepteur sint</p>
  <p class="about-quote outline-heading">"IN DORIAN WE TRUST"</p>
</section>

<section class="pillars">
  <div class="pillar pillar-tech">
    <h3 class="pillar-title">TECHNICAL/MIND</h3>
    <ul class="pillar-list">
      <li><svg width="44" height="44" viewBox="0 0 44 44" fill="none" stroke="var(--orange)" stroke-width="2"><polygon points="22,4 26,16 39,12 30,22 39,32 26,28 22,40 18,28 5,32 14,22 5,12 18,16"/></svg>FIGHTS</li>
      <li><svg width="56" height="44" viewBox="0 0 56 44" fill="none" stroke="var(--orange)" stroke-width="2"><line x1="8" y1="4" x2="8" y2="40"/><path d="M8 6h26l-6 8 6 8H8"/><line x1="2" y1="40" x2="50" y2="40"/></svg>CHALLENGES</li>
      <li><svg width="44" height="44" viewBox="0 0 44 44" fill="none" stroke="var(--orange)" stroke-width="2"><circle cx="22" cy="22" r="18"/><circle cx="22" cy="22" r="11"/><circle cx="22" cy="22" r="4"/></svg>DRILLS</li>
    </ul>
  </div>
  <div class="pillar pillar-spirit">
    <h3 class="pillar-title">SPIRIT</h3>
    <ul class="pillar-list">
      <li><svg width="44" height="44" viewBox="0 0 44 44" fill="none" stroke="var(--orange)" stroke-width="2"><polygon points="22,4 27,17 40,17 29,25 33,39 22,30 11,39 15,25 4,17 17,17"/></svg>FUN</li>
      <li><svg width="44" height="44" viewBox="0 0 44 44" fill="none" stroke="var(--orange)" stroke-width="2"><circle cx="22" cy="22" r="18"/><ellipse cx="22" cy="22" rx="8" ry="18"/><line x1="4" y1="22" x2="40" y2="22"/></svg>TRIPS</li>
      <li><svg width="44" height="44" viewBox="0 0 44 44" fill="none" stroke="var(--orange)" stroke-width="2"><polyline points="3,38 16,14 25,28 31,20 41,38"/><line x1="3" y1="38" x2="41" y2="38"/></svg>OUTING</li>
    </ul>
  </div>
  <div class="pillar pillar-body">
    <h3 class="pillar-title">BODY</h3>
    <ul class="pillar-list">
      <li><svg width="44" height="44" viewBox="0 0 44 44" fill="none" stroke="var(--orange)" stroke-width="2"><circle cx="22" cy="22" r="18"/><polyline points="13,22 20,29 32,15"/></svg>RECOVERY</li>
      <li><svg width="44" height="44" viewBox="0 0 44 44" fill="none" stroke="var(--orange)" stroke-width="2"><rect x="9" y="6" width="26" height="34" rx="2"/><line x1="15" y1="16" x2="29" y2="16"/><line x1="15" y1="23" x2="29" y2="23"/><line x1="15" y1="30" x2="25" y2="30"/></svg>CONDITIONS</li>
      <li><svg width="44" height="44" viewBox="0 0 44 44" fill="none" stroke="var(--orange)" stroke-width="2"><circle cx="22" cy="25" r="14"/><path d="M22 11c0-4 3-7 7-7"/></svg>NUTRITION</li>
    </ul>
  </div>
</section>

<section class="rules">
  <h2 class="scars-heading outline-heading">I DONT WANT TO DIE WITHOUT ANY SCARS</h2>
  <p class="scars-text">I'm breaking my attachment to physical power and possessions, because only through destroying myself can I discover the greater power of my spirit.</p>

  <div class="rule-card" style="left:128px;top:2376px"><div class="rule-badge">RULE<br>1</div><p class="rule-text">Lorem ipsum dolor sit amet, consectetur adipiscing elit, sed do</p></div>
  <div class="rule-card" style="left:617px;top:2376px"><div class="rule-badge">RULE<br>2</div><p class="rule-text">Lorem ipsum dolor sit amet, consectetur adipiscing elit, sed do</p></div>
  <div class="rule-card" style="left:128px;top:2565px"><div class="rule-badge">RULE<br>3</div><p class="rule-text">Lorem ipsum dolor sit amet, consectetur adipiscing elit, sed do</p></div>
  <div class="rule-card" style="left:617px;top:2565px"><div class="rule-badge">RULE<br>4</div><p class="rule-text">Lorem ipsum dolor sit amet, consectetur adipiscing elit, sed do</p></div>
  <div class="rule-card" style="left:128px;top:2757px"><div class="rule-badge">RULE<br>5</div><p class="rule-text">Lorem ipsum dolor sit amet, consectetur adipiscing elit, sed do</p></div>
  <div class="rule-card" style="left:617px;top:2757px"><div class="rule-badge">RULE<br>6</div><p class="rule-text">Lorem ipsum dolor sit amet, consectetur adipiscing elit, sed do</p></div>
  <div class="rule-card" style="left:128px;top:2948px"><div class="rule-badge">RULE<br>7</div><p class="rule-text">Lorem ipsum dolor sit amet, consectetur adipiscing elit, sed do</p></div>
  <div class="rule-card" style="left:617px;top:2948px"><div class="rule-badge">RULE<br>8</div><p class="rule-text">Lorem ipsum dolor sit amet, consectetur adipiscing elit, sed do</p></div>
</section>

<section class="faq">
  <h2 class="faq-heading outline-heading">COMMON QUESTIONS</h2>
  <div class="faq-q" style="top:3272px">WHY THE "K7" ?
    <svg width="22" height="16" viewBox="0 0 22 16"><polygon points="0,0 22,0 11,16" fill="var(--orange)"/></svg></div>
  <p class="faq-a" style="top:3352px">Lorem ipsum dolor sit amet, consectetur adipiscing elit, sed do eiusmod tempor incididunt ut labore et dolore magna aliqua. Ut enim ad minim veniam, quis nostrud exercitation ullamco laboris nisi ut aliquip ex ea commodo consequat.</p>
  <div class="faq-q" style="top:3499px">HOW DOES SOMEONE GET INVITED
    <svg width="22" height="16" viewBox="0 0 22 16"><polygon points="0,0 22,0 11,16" fill="var(--orange)"/></svg></div>
  <p class="faq-a" style="top:3577px">Lorem ipsum dolor sit amet, consectetur adipiscing elit, sed do eiusmod tempor incididunt ut labore et dolore magna aliqua. Ut enim ad minim veniam, quis nostrud exercitation ullamco laboris nisi ut aliquip ex ea commodo consequat.</p>
  <div class="view-more">VIEW MORE</div>
</section>

<section class="video" role="img" aria-label="Two martial artists mid-kick against orange and blue smoke">
  <div class="video-play"><span class="dot"></span>Vidrelo</div>
</section>

<footer class="site-footer">
  <div class="footer-brand">ORDER<br>VANTAGE</div>
  <div class="social">
    <span><i></i>Pixtrelle</span>
    <span><i></i>Chatterloop</span>
    <span><i></i>Flitbird</span>
  </div>
  <p class="copyright">@2023 COPYRIGHTS. ORDER VANTAGE. ALL RIGHTS RESERVED.</p>
</footer>

</body>
</html>
```